2022 Landscaping Services

Please use the prior year design as an example. Similar style but DO NOT COPY IT EXACTLY- you can use different photos from our website if you like. Same text for year 2022.
Design should clearly depict the differences between the 3 products so people can buy one of them. Be creative!

size 8.5" x 11"

Must provide source file in photoshop if you are winner

Requirements
Must have
• Same text as original flier but with year 2022

```html
<!DOCTYPE html>
<html lang="en">
<head>
<meta charset="utf-8">
<title>Maplewood Cemetery – 2022 Gravesite Landscaping Packages</title>
<link rel="stylesheet" href="https://fonts.googleapis.com/css2?family=Montserrat:ital,wght@0,400;0,500;0,600;0,700;0,800;1,800&display=swap">
<style>
  :root{
    --maroon:#8c161c;
    --maroon-bright:#c1272d;
    --ink:#2b2b2b;
    --paper:#ffffff;
    --mist:#edf4fa;
    --rule:#d5d9de;
    --rule-red:#a9343a;
    --grass:#5d8a35;
    --grass-dark:#3f6526;
    --stone:#c9ccc6;
  }
  *{box-sizing:border-box;margin:0;padding:0}
  html,body{width:963px;height:1200px;overflow:hidden;background:var(--paper)}
  body{font-family:"Montserrat",Arial,sans-serif;color:var(--ink);position:relative}

  .hero{position:absolute;left:0;top:0;width:963px;height:426px;
    background:linear-gradient(180deg,#fff 0%,#fff 30%,rgba(255,255,255,0) 52%),
      radial-gradient(ellipse at 20% 80%,var(--grass-dark) 0%,rgba(63,101,38,0) 45%),
      linear-gradient(180deg,var(--stone) 40%,var(--grass) 70%,var(--grass-dark) 100%);}
  .brand{position:absolute;top:66px;left:0;width:100%;display:flex;justify-content:center;align-items:center;gap:14px}
  .brand-mark{width:46px;height:46px;border:2px solid var(--maroon);border-radius:50%}
  .brand-name{font-weight:600;font-size:30px;letter-spacing:1px;color:var(--maroon);text-transform:uppercase}

  .title-band{position:absolute;left:0;top:426px;width:963px;height:151px;background:var(--maroon);
    color:#fff;text-align:center;padding-top:20px;font-size:39px;line-height:48px;font-weight:400;letter-spacing:.5px}
  .title-band strong{font-weight:800}

  .compare{position:absolute;left:0;top:577px;width:963px;height:568px;background:var(--mist)}
  .card-basic{position:absolute;left:228px;top:47px;width:430px;height:470px;background:#fff;box-shadow:0 2px 6px rgba(0,0,0,.12)}
  .card-perpetual{position:absolute;left:660px;top:20px;width:259px;height:523px;background:var(--maroon);box-shadow:0 2px 8px rgba(0,0,0,.2)}
  .badge{position:absolute;left:628px;top:-29px;width:78px;height:78px;border-radius:50%;
    background:radial-gradient(circle at 40% 35%,#d8363d,var(--maroon-bright) 55%,#8e1a1f);
    box-shadow:0 3px 6px rgba(0,0,0,.3);color:#fff;font-weight:800;font-style:italic;font-size:11px;
    line-height:13px;text-align:center;padding-top:25px;z-index:2}

  .grid{position:absolute;left:40px;top:47px;width:879px;display:grid;
    grid-template-columns:188px 215px 215px 2px 259px;
    grid-template-rows:82px 57px 45px 35px 36px 45px 46px 34px 90px}
  .cell{display:flex;flex-direction:column;align-items:center;justify-content:center;text-align:center;border-top:1px solid var(--rule)}
  .cell.perp{color:#fff;border-top-color:var(--rule-red)}
  .cell.head{border-top:none}
  .gap{border:none}
  .service{font-weight:700;font-size:11px;line-height:13.5px;letter-spacing:.3px}
  .services-head{font-weight:800;font-size:18px;line-height:22px;color:var(--maroon);border-top:none}
  .plan-name{font-weight:800;font-size:18px;color:var(--maroon);line-height:22px}
  .plan-sub{font-size:14px;font-weight:500;letter-spacing:.3px;line-height:20px}
  .perp .plan-name{color:#fff;font-size:24px;line-height:28px;margin-top:-16px}
  .perp .plan-sub{font-size:19px}
  .note{font-size:8.5px;font-weight:600;line-height:10.5px}
  .icon{width:16px;height:16px}
  .valid{font-weight:700;font-size:14px;color:var(--maroon);line-height:18px;border-top:none}
  .prices{font-weight:700;font-size:13px;color:var(--maroon);display:flex;gap:7px;align-items:baseline}
  .years{display:flex;gap:30px;font-size:6.5px;font-weight:600;margin:2px 0 8px}
  .big-price{font-size:23px;font-weight:800;color:var(--maroon);margin-bottom:6px}
  .perp .big-price{color:#fff;font-size:28px}
  .perp .note{font-size:9px;line-height:11px}

  .footer{position:absolute;left:0;top:1145px;width:963px;height:55px;background:var(--maroon);color:#fff;
    display:flex;align-items:center;justify-content:center;gap:22px;font-size:14px;font-weight:500;letter-spacing:.3px}
  .footer span{display:flex;align-items:center;gap:10px}
  .divider{width:1px;height:22px;background:#fff}
  .footer svg{width:14px;height:14px;fill:#fff}
</style>
</head>
<body>
<svg width="0" height="0" style="position:absolute">
  <symbol id="no" viewBox="0 0 16 16"><circle cx="8" cy="8" r="6.5" fill="none" stroke="currentColor" stroke-width="2"/><line x1="3.5" y1="12.5" x2="12.5" y2="3.5" stroke="currentColor" stroke-width="2"/></symbol>
  <symbol id="tick" viewBox="0 0 16 16"><path d="M2 9 L6 13 L14 2" fill="none" stroke="currentColor" stroke-width="2.2" stroke-linecap="round" stroke-linejoin="round"/></symbol>
</svg>

<header class="hero" role="img" aria-label="Photograph of cemetery grounds with green lawns, hedges, headstones and a tree">
  <div class="brand"><span class="brand-mark"></span><span class="brand-name">Maplewood Cemetery</span></div>
</header>

<section class="title-band"><strong>2022</strong> GRAVESITE LANDSCAPING<br>PACKAGES</section>

<section class="compare">
  <div class="card-basic"></div>
  <div class="card-perpetual"></div>
  <div class="badge">MOST<br>POPULAR</div>

  <div class="grid" style="color:#2b2b2b">
    <div class="cell services-head">SERVICES<br>OFFERED</div>
    <div class="cell head"><div class="plan-name">SEASONAL</div><div class="plan-sub">CARE ENDOWMENT</div></div>
    <div class="cell head"><div class="plan-name">BASIC</div><div class="plan-sub">CARE ENDOWMENT</div></div>
    <div class="gap"></div>
    <div class="cell head perp"><div class="plan-name">PERPETUAL</div><div class="plan-sub">CARE ENDOWMENT</div></div>

    <div class="cell service">WEDDING &amp; TRIMMING<br>ON YOUR GRAVESITE</div>
    <div class="cell note">Approximately every 7 weeks<br>during the growing season:<br>Mid-April through Mid-October</div>
    <div class="cell note">2 times per year:<br>Mid-May &amp; Mid-September</div>
    <div class="gap"></div>
    <div class="cell note perp">Approximately every 7 weeks<br>during the growing season:<br>Mid-April through Mid-October</div>

    <div class="cell service">PAYMENT ENSURED<br>FOREVER GRAVE CARE</div>
    <div class="cell"><svg class="icon"><use href="#no"/></svg></div>
    <div class="cell" style="color:var(--maroon)"><svg class="icon"><use href="#tick"/></svg></div>
    <div class="gap"></div>
    <div class="cell perp"><svg class="icon"><use href="#tick"/></svg></div>

    <div class="cell service">MONUMENT LEVELING</div>
    <div class="cell"><svg class="icon"><use href="#no"/></svg></div>
    <div class="cell" style="color:var(--maroon)"><svg class="icon"><use href="#tick"/></svg></div>
    <div class="gap"></div>
    <div class="cell perp"><svg class="icon"><use href="#tick"/></svg></div>

    <div class="cell service">MONUMENT CLEANING</div>
    <div class="cell"><svg class="icon"><use href="#no"/></svg></div>
    <div class="cell"><svg class="icon"><use href="#no"/></svg></div>
    <div class="gap"></div>
    <div class="cell perp"><svg class="icon"><use href="#tick"/></svg></div>

    <div class="cell service">FULL BED OF<br>BOXWOOD SHRUBS</div>
    <div class="cell"><svg class="icon"><use href="#no"/></svg></div>
    <div class="cell"><svg class="icon"><use href="#no"/></svg></div>
    <div class="gap"></div>
    <div class="cell perp"><svg class="icon"><use href="#tick"/></svg></div>

    <div class="cell service">REPLACEMENT OF<br>SHRUBS</div>
    <div class="cell"><svg class="icon"><use href="#no"/></svg></div>
    <div class="cell"><svg class="icon"><use href="#no"/></svg></div>
    <div class="gap"></div>
    <div class="cell perp"><svg class="icon"><use href="#tick"/></svg></div>

    <div class="cell service">TRUST CERTIFICATE</div>
    <div class="cell"><svg class="icon"><use href="#no"/></svg></div>
    <div class="cell"><svg class="icon"><use href="#no"/></svg></div>
    <div class="gap"></div>
    <div class="cell perp"><svg class="icon"><use href="#tick"/></svg></div>

    <div class="cell valid">Valid through<br>10/31/21</div>
    <div class="cell">
      <div class="prices"><span>$357</span>|<span>$238</span>|<span>$119</span></div>
      <div class="years"><span>3 Years</span><span>2 Years</span><span>1 Year</span></div>
      <div class="note">Multi-year paymentslocks<br>in current rates</div>
    </div>
    <div class="cell"><div class="big-price">$255</div><div class="note">12 Monthly payments.<br>Call for single payment discounts.</div></div>
    <div class="gap"></div>
    <div class="cell perp"><div class="big-price">$313</div><div class="note">12 Monthly payments.<br>Call for single payment discounts.</div></div>
  </div>
</section>

<footer class="footer">
  <span><svg viewBox="0 0 16 16"><path d="M8 0a5.5 5.5 0 0 0-5.5 5.5C2.5 10 8 16 8 16s5.5-6 5.5-10.5A5.5 5.5 0 0 0 8 0zm0 7.8a2.3 2.3 0 1 1 0-4.6 2.3 2.3 0 0 1 0 4.6z"/></svg>48 Elm Ave. Fairview NJ 07022</span>
  <i class="divider"></i>
  <span><svg viewBox="0 0 16 16"><path d="M3.6 1l2.6 3-1.5 2a9 9 0 0 0 4.7 4.7l2-1.5 3 2.6-1.4 2.6C7.5 15 1 8.5 1 2.4z"/></svg>(555) 318-4270</span>
  <i class="divider"></i>
  <span><svg viewBox="0 0 16 16"><path d="M8 .5a7.5 7.5 0 1 0 0 15 7.5 7.5 0 0 0 0-15zm0 1.4c.8.8 1.5 2.3 1.8 4.4H6.2C6.5 4.2 7.2 2.7 8 1.9zM2 7.3h2.8a15 15 0 0 0 .2 2.4H2.3A6 6 0 0 1 2 7.3zm1-2.4a6 6 0 0 1 2.6-2.3 9 9 0 0 0-1 2.3zM6.2 9.7a14 14 0 0 1-.2-2.4h4a14 14 0 0 1-.2 2.4zm5-2.4H14a6 6 0 0 1-.3 2.4H11a15 15 0 0 0 .2-2.4zm.2-2.4a9 9 0 0 0-1-2.3A6 6 0 0 1 13 4.9zM3 11h1.8a8 8 0 0 0 .8 2.4A6 6 0 0 1 3 11zm3.4 0h3.2c-.3 1.6-.9 2.6-1.6 3.3-.7-.7-1.3-1.7-1.6-3.3zm4 2.4a8 8 0 0 0 .8-2.4H13a6 6 0 0 1-2.6 2.4z"/></svg>www.maplewoodcemetery.com</span>
</footer>
</body>
</html>
```